business card

Business card for new business.
Red and black corporate colors.
Card can have an Indsutrial feel to it. Feel free to add Rust, Bolted steel, or graphics as you see fit. We provide highly specialized services to the below mentioned industries.
Keep information out of corners so that if I want I can choose rounded corners.
Information
- front. name - title - phone - email
- Rear
Refining - Rail - Infrastructure - Mining - Energy
Calgary - Edmonton - Fort McMurray - Revelstoke - Vancouver

```html
<!DOCTYPE html>
<html lang="en">
<head>
<meta charset="utf-8">
<title>Girderline business card</title>
<link rel="stylesheet" href="https://fonts.googleapis.com/css2?family=Roboto:wght@400;500&family=Roboto+Condensed:wght@700&display=swap">
<style>
  :root {
    --red: #e2001a;
    --ink: #1a1b1d;
    --paper: #f4f4f4;
    --steel: #6e6e6e;
    --white: #ffffff;
    --backdrop: #e6e3de;
  }
  * { margin: 0; padding: 0; box-sizing: border-box; }
  html, body { width: 1200px; height: 960px; overflow: hidden; }
  body {
    background: var(--backdrop);
    font-family: "Roboto", Arial, sans-serif;
    position: relative;
  }
  .card {
    position: absolute;
    width: 600px;
    height: 342px;
    overflow: hidden;
    box-shadow: 0 3px 8px rgba(0,0,0,0.25);
  }
  .card--front { left: 314px; top: 113px; background: var(--paper); }
  .card--back { left: 311px; top: 472px; background: var(--ink); }

  .front-panel { position: absolute; inset: 0; }

  .wordmark {
    font-family: "Roboto Condensed", "Arial Narrow", sans-serif;
    font-weight: 700;
    color: var(--steel);
    letter-spacing: 0.5px;
    position: absolute;
    display: flex;
    align-items: center;
    line-height: 1;
  }
  .wordmark__mark { background: var(--red); display: block; }
  .wordmark--front { left: 48px; top: 48px; font-size: 42px; gap: 10px; }
  .wordmark--front .wordmark__mark { width: 14px; height: 14px; }
  .wordmark--back { left: 0; right: 0; top: 120px; justify-content: center; font-size: 56px; gap: 14px; }
  .wordmark--back .wordmark__mark { width: 18px; height: 18px; }

  .identity {
    position: absolute;
    right: 58px;
    top: 130px;
    text-align: right;
    color: var(--white);
  }
  .identity__name { font-weight: 500; font-size: 22px; line-height: 1.1; letter-spacing: 0.2px; }
  .identity__title { font-size: 15px; margin-top: 3px; letter-spacing: 0.3px; }

  .contact {
    position: absolute;
    right: 58px;
    top: 244px;
    list-style: none;
    color: var(--white);
    font-size: 14px;
    text-align: right;
  }
  .contact__item { display: flex; justify-content: flex-end; align-items: center; gap: 6px; height: 19.5px; }
  .contact__icon { width: 12px; height: 12px; fill: var(--white); flex: none; }

  .sector-band {
    position: absolute;
    left: 0; right: 0;
    top: 246px;
    height: 74px;
    background: var(--red);
    color: var(--white);
    font-size: 14.5px;
    line-height: 18px;
    text-align: center;
    padding-top: 10px;
  }
</style>
</head>
<body>

<section class="card card--front" aria-label="Card front">
  <svg class="front-panel" viewBox="0 0 600 342" width="600" height="342" aria-hidden="true">
    <polygon points="356,25 600,25 600,342 0,342 0,318 259,322" fill="var(--red)"/>
  </svg>

  <div class="wordmark wordmark--front">
    <span class="wordmark__text">GIRDERLINE</span>
    <span class="wordmark__mark"></span>
  </div>

  <div class="identity">
    <p class="identity__name">EVAN HOLT</p>
    <p class="identity__title">CEO/FOUNDER</p>
  </div>

  <ul class="contact">
    <li class="contact__item">555 210 4837
      <svg class="contact__icon" viewBox="0 0 24 24" aria-hidden="true"><path d="M6.6 10.8a15 15 0 0 0 6.6 6.6l2.2-2.2a1 1 0 0 1 1-.25 11.4 11.4 0 0 0 3.6.57 1 1 0 0 1 1 1V20a1 1 0 0 1-1 1A17 17 0 0 1 3 4a1 1 0 0 1 1-1h3.5a1 1 0 0 1 1 1c0 1.250.2 2.450.57 3.570a1 1 0 0 1-.25 1z"/></svg>
    </li>
    <li class="contact__item">info@girderline.com
      <svg class="contact__icon" viewBox="0 0 24 24" aria-hidden="true"><path d="M2 5h20v14H2z M2 5l10 8 10-8" fill="var(--white)" stroke="var(--red)" stroke-width="1.5"/></svg>
    </li>
    <li class="contact__item">www.girderline.com
      <svg class="contact__icon" viewBox="0 0 24 24" aria-hidden="true"><circle cx="12" cy="12" r="11"/><path d="M1 12h22M12 1c-4 4-4 18 0 22M12 1c4 4 4 18 0 22" fill="none" stroke="var(--red)" stroke-width="1.6"/></svg>
    </li>
  </ul>
</section>

<section class="card card--back" aria-label="Card back">
  <div class="wordmark wordmark--back">
    <span class="wordmark__text">GIRDERLINE</span>
    <span class="wordmark__mark"></span>
  </div>

  <div class="sector-band">
    <p>Pipelines • Transit • Utilities • Forestry</p>
    <p>Marine • Northvale • Ashcombe • Port Halden Falls</p>
    <p>Kestrel Bay • Millbrook</p>
  </div>
</section>

</body>
</html>
```